Harlow Mechanical Contractors needs a Website

Create basic website for commercial plumbing and mechanical contractor; to include pictures of works in progress and completed works, description of all services offered and geographical locations and licenses

Target Market(s)

General Contractors, Real Estate Developers, Construction Companies

Industry/Entity Type

Construction

Coding

Coded - Design and coding required

Number of Pages Required

5+ page

• See logo attached to project

Colors
0392cd

```html
<!DOCTYPE html>
<html lang="en">
<head>
<meta charset="utf-8">
<title>Harlow Mechanical Contractors</title>
<link rel="stylesheet" href="https://fonts.googleapis.com/css2?family=Oswald:wght@400;500&family=Roboto:wght@400;500;700&display=swap">
<style>
:root{
  --brand:#1f5d84;
  --brand-dark:#184c6d;
  --brand-deep:#1a5579;
  --accent:#2a6f9d;
  --ink:#222;
  --muted:#7a7a7a;
  --rule:#e3e3e3;
  --footer-ink:#d9e6ef;
  --black:#111;
  --white:#fff;
}
*{box-sizing:border-box;margin:0;padding:0}
html,body{width:1200px;height:3005px;overflow:hidden}
body{font-family:"Roboto",Arial,sans-serif;color:var(--ink);background:var(--white);position:relative}
a{color:inherit;text-decoration:none}

.topbar{height:52px;background:var(--brand);color:var(--white);display:flex;align-items:center;justify-content:space-between;padding:0 90px;font-size:13px}
.topbar .contact{display:flex;gap:22px;align-items:center}
.topbar .contact span{display:flex;align-items:center;gap:6px}
.social-squares{display:flex;gap:6px}
.social-squares i{width:14px;height:14px;background:var(--white);border-radius:2px;display:block}

.header{height:132px;display:flex;align-items:center;justify-content:space-between;padding:0 96px 0 92px}
.brand-name{display:flex;align-items:center;gap:10px;color:var(--brand);font-weight:700;font-size:17px;line-height:1.05;text-transform:uppercase;width:220px}
.brand-name .dot{width:40px;height:40px;border-radius:50%;background:var(--brand);flex:none}
.nav{display:flex;align-items:center;gap:38px;font-size:15px;color:#444;text-transform:uppercase}
.nav a.active{color:var(--accent)}
.nav .search{width:36px;height:34px;border:2px solid #555;border-radius:3px;display:flex;align-items:center;justify-content:center;margin-left:-6px}

.hero{height:572px;position:relative;background:linear-gradient(180deg,#8fb4d6 0%,#c9d4dc 40%,#9a7e6c 75%,#5e5650 100%)}
.hero-title{position:absolute;left:88px;top:556px;top:372px;padding:18px 28px 14px;background:rgba(30,30,30,.45);font-family:"Oswald",sans-serif;color:var(--white);text-transform:uppercase}
.hero-title h1{font-size:48px;font-weight:400;line-height:1.05}
.hero-title p{font-size:36px;line-height:1.15}
.hero-dots{position:absolute;right:96px;bottom:30px;display:flex;gap:8px}
.hero-dots i{width:10px;height:10px;border-radius:50%;background:var(--white);display:block}

.welcome{height:439px;background:linear-gradient(135deg,var(--brand-deep),var(--brand-dark));color:var(--white);text-align:center;padding-top:52px}
.welcome h2{font-size:27px;font-weight:500;text-transform:uppercase}
.welcome p{width:1010px;margin:16px auto 0;font-size:13.5px;line-height:22px}

.sectors{position:absolute;top:978px;left:90px;display:flex;gap:22px}
.sector{width:326px;height:324px;position:relative;box-shadow:0 14px 18px rgba(0,0,0,.25);border-radius:4px;overflow:hidden}
.sector .photo{position:absolute;inset:0}
.sector .caption{position:absolute;left:0;right:0;bottom:0;height:100px;background:rgba(20,20,20,.75);color:var(--white);text-align:center;padding-top:20px}
.sector h3{font-size:16px;font-weight:500;text-transform:uppercase}
.sector p{font-size:12.5px;line-height:18px;margin-top:6px;padding:0 40px}

.services{position:absolute;top:1370px;left:0;width:1200px;text-align:center}
.section-title{font-size:28px;font-weight:500;text-transform:uppercase;color:var(--ink)}
.section-title span{color:var(--accent)}
.service-list{display:flex;justify-content:center;gap:46px;margin-top:64px}
.service{width:220px}
.service .icon{width:90px;height:90px;margin:0 auto;border-radius:50%;background:var(--brand);display:flex;align-items:center;justify-content:center;box-shadow:0 16px 12px -12px rgba(0,0,0,.25)}
.service h4{margin-top:56px;font-size:17px;font-weight:500;text-transform:uppercase}
.service p{margin-top:8px;font-size:13px;line-height:19px;color:var(--muted)}

.plumbing{position:absolute;top:1762px;left:0;width:1200px;height:443px;background:linear-gradient(90deg,#eef3f7 0%,#dfe8ef 40%,#8a9fb3 62%,#6f8296 100%)}
.plumbing .copy{position:absolute;left:90px;top:120px;width:420px}
.plumbing h2{font-size:34px;font-weight:500;color:var(--accent);text-transform:uppercase}
.plumbing p{font-size:14px;line-height:22px;color:#333;margin-top:10px}
.button{display:inline-block;margin-top:18px;width:132px;height:44px;line-height:44px;text-align:center;background:var(--accent);color:var(--white);font-size:14px;text-transform:uppercase;border-radius:2px}

.news{position:absolute;top:2265px;left:0;width:1200px}
.news .section-title{text-align:center}
.news-list{display:flex;gap:34px;padding-left:92px;margin-top:30px}
.post{width:320px}
.post .thumb{height:196px;border:5px solid #f0f0f0;box-shadow:0 1px 3px rgba(0,0,0,.2);position:relative}
.post .thumb .photo{position:absolute;inset:0}
.date{position:absolute;left:0;top:50px;width:50px;text-align:center;color:var(--white)}
.date .day{background:var(--brand);font-size:19px;font-weight:500;line-height:26px}
.date .mon{background:var(--brand);font-size:11px;line-height:16px;text-transform:uppercase}
.date .yr{background:#1b1b1b;font-size:13px;line-height:28px;margin-top:6px}
.post h5{font-size:14.5px;font-weight:400;margin-top:14px;color:#333}
.post p{font-size:12px;line-height:17px;color:var(--muted);margin-top:8px}
.post .more{display:block;font-size:12px;color:var(--accent);margin-top:12px}

.footer{position:absolute;top:2686px;left:0;width:1200px;height:219px;background:var(--brand);color:var(--footer-ink);display:flex;padding:44px 0 0 90px;font-size:12px}
.footer h6{font-size:14px;font-weight:500;color:var(--white);text-transform:uppercase;margin-bottom:18px}
.footer .col-links{width:210px}
.footer .col-links li{list-style:none;line-height:24px;padding-left:10px;position:relative}
.footer .col-links li:before{content:"";position:absolute;left:0;top:8px;border-left:5px solid var(--footer-ink);border-top:4px solid transparent;border-bottom:4px solid transparent}
.footer .col-about{width:352px}
.footer .col-about p{line-height:20px;width:270px}
.footer .col-contact{width:256px;line-height:24px}
.footer .col-news p{width:180px;line-height:18px}
.signup{display:flex;margin-top:14px}
.signup .field{width:146px;height:30px;background:var(--white);color:#999;font-size:10px;line-height:30px;padding-left:12px}
.signup .submit{width:56px;height:30px;background:var(--black);color:var(--white);font-size:12px;line-height:30px;text-align:center}

.bottombar{position:absolute;top:2905px;left:0;width:1200px;height:100px;background:var(--black);color:var(--white);display:flex;align-items:center;justify-content:space-between;padding:0 86px 0 90px;font-size:12px}
.bottombar .circles{display:flex;gap:20px}
.bottombar .circles i{width:36px;height:36px;border:2px solid var(--white);border-radius:50%;display:block}
</style>
</head>
<body>

<div class="topbar">
  <div class="contact">
    <span><svg width="12" height="12" viewBox="0 0 24 24"><path fill="#fff" d="M6.6 10.8a15.1 15.1 0 0 0 6.6 6.6l2.2-2.2c.3-.3.7-.4 1-.2 1.1.4 2.3.6 3.6.6.6 0 1 .4 1 1V20c0 .6-.4 1-1 1A17 17 0 0 1 3 4c0-.6.4-1 1-1h3.5c.6 0 1 .4 1 1 0 1.3.2 2.5.6 3.6.1.3 0 .7-.2 1z"/></svg>: 0400 555 218</span>
    <span><svg width="13" height="10" viewBox="0 0 26 20"><rect width="26" height="20" rx="2" fill="#fff"/><path d="M1 2l12 9 12-9" stroke="#1f5d84" stroke-width="2" fill="none"/></svg>: info@harlowmech.com</span>
  </div>
  <div class="social-squares"><i></i><i></i><i></i><i></i></div>
</div>

<header class="header">
  <div class="brand-name"><span class="dot"></span><span>Harlow Mechanical Contractors</span></div>
  <nav class="nav">
    <a class="active" href="#">Home</a><a href="#">About</a><a href="#">Services</a><a href="#">Projects</a><a href="#">News</a><a href="#">Contacts</a>
    <span class="search"><svg width="14" height="14" viewBox="0 0 24 24"><circle cx="10" cy="10" r="7" stroke="#444" stroke-width="3" fill="none"/><path d="M15 15l6 6" stroke="#444" stroke-width="3"/></svg></span>
  </nav>
</header>

<section class="hero" role="img" aria-label="Photo of a completed multi-storey residential building with white balconies and brick facade under a blue sky">
  <div class="hero-title"><h1>Commercial Plumbing</h1><p>and Mechanical Contractor</p></div>
  <div class="hero-dots"><i></i><i></i><i></i><i></i></div>
</section>

<section class="welcome">
  <h2>Welcome to Harlow Mechanical Contractors</h2>
  <p>Lorem Ipsum has been the industry's standard dummy text ever since the 1500s, when an unknown printer took a galley of type and scrambled it to make a type specimen book. It has survived not only five centuries, but also the leap into electronic typesetting, remaining essentially unchanged. It was popularised in the 1960s with the release of Typeset sheets containing Lorem Ipsum passages, and more recently with desktop publishing software like PageForge including</p>
</section>

<div class="sectors">
  <article class="sector">
    <div class="photo" role="img" aria-label="Photo of a bright open-plan large office interior" style="background:linear-gradient(180deg,#e8e4dc,#b9b0a2 60%,#6d6258)"></div>
    <div class="caption"><h3>Large Offices</h3><p>Lorem Ipsum has been the industry's standard dummy text ever since the 1500s,</p></div>
  </article>
  <article class="sector">
    <div class="photo" role="img" aria-label="Photo of condominium towers against a cloudy blue sky" style="background:linear-gradient(180deg,#8fb5db,#c5cfd6 50%,#8a7a6e)"></div>
    <div class="caption"><h3>Condominiums</h3><p>Lorem Ipsum has been the industry's standard dummy text ever since the 1500s,</p></div>
  </article>
  <article class="sector">
    <div class="photo" role="img" aria-label="Photo of two engineers in hard hats reviewing plans at an industrial site" style="background:linear-gradient(180deg,#a9c6e2,#7d8ea0 55%,#3e4a57)"></div>
    <div class="caption"><h3>Industrial Projects</h3><p>Lorem Ipsum has been the industry's standard dummy text ever since the 1500s,</p></div>
  </article>
</div>

<section class="services">
  <h2 class="section-title">Our <span>Services</span></h2>
  <div class="service-list">
    <div class="service">
      <div class="icon"><svg width="26" height="32" viewBox="0 0 26 32"><rect x="2" y="2" width="22" height="28" rx="2" fill="#fff"/><g fill="#1f5d84"><rect x="6" y="6" width="4" height="4"/><rect x="16" y="6" width="4" height="4"/><rect x="6" y="13" width="4" height="4"/><rect x="16" y="13" width="4" height="4"/><rect x="10" y="22" width="6" height="8"/></g></svg></div>
      <h4>Porro Quisquam</h4><p>Lorem Ipsum has been the industry's standard dummy text ever since the 1500s, when an unknown printer</p>
    </div>
    <div class="service">
      <div class="icon"><svg width="22" height="30" viewBox="0 0 22 30"><path d="M11 1C11 1 2 13 2 19a9 9 0 0 0 18 0C20 13 11 1 11 1z" fill="#fff"/></svg></div>
      <h4>Porro Quisquam</h4><p>Lorem Ipsum has been the industry's standard dummy text ever since the 1500s, when an unknown printer</p>
    </div>
    <div class="service">
      <div class="icon"><svg width="32" height="28" viewBox="0 0 32 28"><path d="M16 2L2 14h4v12h8v-8h4v8h8V14h4z" fill="#fff"/></svg></div>
      <h4>Porro Quisquam</h4><p>Lorem Ipsum has been the industry's standard dummy text ever since the 1500s, when an unknown printer</p>
    </div>
    <div class="service">
      <div class="icon"><svg width="30" height="30" viewBox="0 0 30 30"><path d="M27 8a7 7 0 0 1-9.5 6.5L6 26a2.8 2.8 0 0 1-4-4L13.5 10.5A7 7 0 0 1 22 1l-4.5 4.5 1 4 4 1z" fill="#fff"/></svg></div>
      <h4>Porro Quisquam</h4><p>Lorem Ipsum has been the industry's standard dummy text ever since the 1500s, when an unknown printer</p>
    </div>
  </div>
</section>

<section class="plumbing" role="img" aria-label="Photo of a smiling plumber fitting black drain pipes under a sink">
  <div class="copy">
    <h2>Plumbing Services</h2>
    <p>Lorem Ipsum has been the industry's standard dummy text ever since the 1500s, when an unknown printer took a galley of type and scrambled it to make a type specimen book.</p>
    <p>It has survived not only five centuries, but also the leap into electronic typesetting, remaining essentially unchanged.</p>
    <a class="button" href="#">View More</a>
  </div>
</section>

<section class="news">
  <h2 class="section-title">Latest <span>News</span></h2>
  <div class="news-list">
    <article class="post">
      <div class="thumb"><div class="photo" role="img" aria-label="Photo of two workers in hard hats reading plans in a warehouse" style="background:linear-gradient(135deg,#c9a679,#8d7258 50%,#3c4754)"></div>
        <div class="date"><div class="day">02</div><div class="mon">Jun</div><div class="yr">2016</div></div></div>
      <h5>Neque porro quisquam est qui dolorem</h5>
      <p>Lorem Ipsum has been the industry's standard dummy text ever since the 1500s, when an unknown printer took a galley of type and scrambled it to make a type specimen book.</p>
      <a class="more" href="#">Read More »</a>
    </article>
    <article class="post">
      <div class="thumb"><div class="photo" role="img" aria-label="Photo of plumbing tools laid on a kitchen floor plan" style="background:linear-gradient(135deg,#e9ecef,#c8cfd6 50%,#b4886a)"></div>
        <div class="date"><div class="day">02</div><div class="mon">Jun</div><div class="yr">2016</div></div></div>
      <h5>Neque porro quisquam est qui dolorem</h5>
      <p>Lorem Ipsum has been the industry's standard dummy text ever since the 1500s, when an unknown printer took a galley of type and scrambled it to make a type specimen book.</p>
      <a class="more" href="#">Read More »</a>
    </article>
    <article class="post">
      <div class="thumb"><div class="photo" role="img" aria-label="Photo of hands fitting a pipe valve beside a yellow hard hat" style="background:linear-gradient(135deg,#a79b8d,#7d7064 50%,#d6b23a)"></div>
        <div class="date"><div class="day">02</div><div class="mon">Jun</div><div class="yr">2016</div></div></div>
      <h5>Neque porro quisquam est qui dolorem</h5>
      <p>Lorem Ipsum has been the industry's standard dummy text ever since the 1500s, when an unknown printer took a galley of type and scrambled it to make a type specimen book.</p>
      <a class="more" href="#">Read More »</a>
    </article>
  </div>
</section>

<footer class="footer">
  <div class="col-links">
    <h6>Links</h6>
    <ul><li>Customer Support</li><li>Documentation</li><li>Resources</li><li>General FAQs</li></ul>
  </div>
  <div class="col-about">
    <h6>Commercial Plumbing</h6>
    <p>It has survived not only five centuries, but also the leap into electronic typesetting, remaining essentially unchanged. It was popularised in the 1960s with the release of Typeset sheets containing Lorem Ipsum passages,</p>
  </div>
  <div class="col-contact">
    <h6>Get in Touch</h6>
    <div>Address : 1250 Riverside Ave,</div>
    <div>Eastfield, NJ</div>
    <div>Phone : 201 555 0147</div>
    <div>Email : info@harlowmech.com</div>
  </div>
  <div class="col-news">
    <h6>Newsletter</h6>
    <p>Your about us information would fit here nicely.</p>
    <div class="signup"><span class="field">Email address</span><span class="submit">Submit</span></div>
  </div>
</footer>

<div class="bottombar">
  <span>Copyright © 2016. All Rights Reserved</span>
  <div class="circles"><i></i><i></i><i></i></div>
</div>

</body>
</html>
```